Business card for Sports Apparel business

DOUBLE SIDED DESIGN
We need business cards for a new sports apparel business. We are developing a protective headband for soccer initially.
Torvalle is focused on designing and developing head protection products to reduce the likelihood of concussion when playing sports. Exploring and understanding medical insights, material science research, current and former players experiences and governing bodies guidelines has allowed Torvalle to develop the safety, style, form and function requirements of a suitable product to bring to market.
Target Market(s)
Mums buying kits for the sons and daughters. Amateur footballers.
Industry/Entity Type
Sporting Good
Contact Information for Business Card
Martin Ashworth - CEO
Mobile: +44 7431589027
Email: martin@torvalle.co.uk
Tel: 0208 5519372
Helena Pargeter - COO
Mob: +44 7385 640117
Email: helena@torvalle.co.uk
Tel: 0208 5519372
Duncan Farrow - CCO
Mob: +44 7564 293081
Email: duncan@torvalle.co.uk
Tel: 0208 5519372
Look and feel
Each slider illustrates characteristics of the customer's brand and the style your logo design should communicate.

```html
<!DOCTYPE html>
<html lang="en">
<head>
<meta charset="utf-8">
<title>Torvalle Business Card</title>
<link href="https://fonts.googleapis.com/css2?family=Raleway:wght@600;700&family=Arimo:wght@400&display=swap" rel="stylesheet">
<style>
  :root {
    --backdrop: #b9b9b9;
    --card-white: #ffffff;
    --brand-blue: #0b5c99;
    --stripe-grey: #5b5b5b;
    --ink: #333333;
    --pitch-light: #2a8578;
    --pitch-dark: #176a60;
    --shadow: rgba(0, 0, 0, 0.35);
  }
  * { margin: 0; padding: 0; box-sizing: border-box; }
  html, body { width: 1200px; height: 802px; overflow: hidden; background: var(--backdrop); }
  .canvas { position: relative; width: 1200px; height: 802px; }

  .card {
    position: absolute;
    top: 274px;
    width: 443px;
    height: 264px;
    box-shadow: 2px 3px 6px var(--shadow);
    overflow: hidden;
  }

  /* Front */
  .card-front { left: 136px; background: var(--card-white); }
  .front-band { position: absolute; left: 0; top: 0; width: 50px; height: 100%; background: var(--brand-blue); }
  .front-stripe { position: absolute; left: 50px; top: 0; width: 5px; height: 100%; background: var(--stripe-grey); }
  .front-wordmark {
    position: absolute; left: 203px; top: 42px; width: 193px;
    font-family: "Raleway", sans-serif; font-weight: 700; font-size: 31px;
    letter-spacing: 1px; color: var(--brand-blue); text-align: center; line-height: 40px;
  }
  .holder-name {
    position: absolute; left: 74px; top: 141px;
    font-family: "Raleway", sans-serif; font-weight: 700; font-size: 15.5px;
    color: var(--brand-blue); letter-spacing: 0.1px;
  }
  .holder-role {
    position: absolute; left: 74px; top: 159px;
    font-family: "Arimo", sans-serif; font-size: 12.5px; color: var(--ink);
  }
  .contact-list { position: absolute; left: 75px; top: 189px; list-style: none; }
  .contact-item {
    display: flex; align-items: center; height: 16.7px;
    font-family: "Arimo", sans-serif; font-size: 12.5px; color: var(--ink);
  }
  .contact-icon { width: 14px; height: 14px; margin-right: 7px; flex: none; }

  /* Back */
  .card-back {
    left: 624px;
    background: linear-gradient(120deg, var(--pitch-dark) 0%, var(--pitch-light) 45%, var(--pitch-dark) 100%);
  }
  .back-photo { position: absolute; inset: 0; }
  .back-wordmark {
    position: absolute; left: 0; top: 104px; width: 100%;
    font-family: "Raleway", sans-serif; font-weight: 700; font-size: 44px;
    letter-spacing: 1.5px; color: var(--card-white); text-align: center; line-height: 58px;
  }
</style>
</head>
<body>
<main class="canvas">
  <section class="card card-front" aria-label="Business card front">
    <div class="front-band"></div>
    <div class="front-stripe"></div>
    <div class="front-wordmark">TORVALLE</div>
    <h1 class="holder-name">MARTIN ASHWORTH</h1>
    <p class="holder-role">CEO</p>
    <ul class="contact-list">
      <li class="contact-item">
        <svg class="contact-icon" viewBox="0 0 14 14" aria-hidden="true">
          <rect x="0.6" y="0.6" width="12.8" height="12.8" rx="1.5" fill="none" stroke="#0b5c99" stroke-width="1.2"/>
          <path d="M4 3.2 l1.6 -0.2 l0.8 2 l-1 0.8 q0.8 1.8 2.6 2.7 l0.8 -1 l2 0.8 l-0.2 1.6 q-4.5 0.5 -6.6 -6.7z" fill="#0b5c99"/>
        </svg>
        0208 5519372
      </li>
      <li class="contact-item">
        <svg class="contact-icon" viewBox="0 0 14 14" aria-hidden="true">
          <rect x="0.6" y="0.6" width="12.8" height="12.8" rx="1.5" fill="none" stroke="#0b5c99" stroke-width="1.2"/>
          <rect x="4.3" y="2.8" width="5.4" height="8.4" rx="0.8" fill="none" stroke="#0b5c99" stroke-width="1"/>
          <circle cx="7" cy="9.9" r="0.5" fill="#0b5c99"/>
        </svg>
        +44 7431589027
      </li>
      <li class="contact-item">
        <svg class="contact-icon" viewBox="0 0 14 14" aria-hidden="true">
          <rect x="0.6" y="0.6" width="12.8" height="12.8" rx="1.5" fill="none" stroke="#0b5c99" stroke-width="1.2"/>
          <rect x="3" y="4" width="8" height="6" fill="#0b5c99"/>
          <path d="M3 4 L7 7.4 L11 4" fill="none" stroke="#ffffff" stroke-width="0.9"/>
        </svg>
        martin@torvalle.co.uk
      </li>
    </ul>
  </section>

  <section class="card card-back" aria-label="Business card back">
    <div class="back-photo" role="img" aria-label="Aerial photograph of a football pitch with players, tinted teal"></div>
    <div class="back-wordmark">TORVALLE</div>
  </section>
</main>
</body>
</html>
```